Water ATM Card

Need a design for water ATM cards. Size of card is 3.375 x 2.125 inch
On the Front include the Cedar hollow Logo.
Bottom right corner should have Price $100
On the Back
This card is to be used to access water refills at any Cedar Hollow Water Vending Machines.
Please contact (869) 418 2930 or (869) 534 1276 or email clearflowbox@mailvista.example for any assistance or recharging of card.

```html
<!DOCTYPE html>
<html lang="en">
<head>
<meta charset="utf-8">
<title>Cedar Hollow Water Card</title>
<link href="https://fonts.googleapis.com/css2?family=Montserrat:wght@700&family=Poppins:wght@400;500;600;700&display=swap" rel="stylesheet">
<style>
  :root {
    --backdrop: #9a9a9a;
    --card: #ffffff;
    --brand-blue: #1a6fb8;
    --navy: #173e8a;
    --green-deep: #1e9a48;
    --green-light: #7dc242;
    --water-mid: #7fa9cc;
    --water-pale: #dcedf6;
  }
  * { margin: 0; padding: 0; box-sizing: border-box; }
  html, body { width: 1093px; height: 1200px; overflow: hidden; }
  body { background: var(--backdrop); position: relative; font-family: "Poppins", sans-serif; }

  .card {
    position: absolute;
    left: 264px;
    width: 580px;
    height: 356px;
    background: var(--card);
    border-radius: 24px;
    overflow: hidden;
  }
  .card--front { top: 226px; }
  .card--back { top: 621px; }

  .water-art { position: absolute; left: 0; bottom: 0; width: 100%; display: block; }
  .card--front .water-art { height: 230px; }
  .card--back .water-art { height: 240px; }

  .brand-name {
    position: absolute;
    left: 20px;
    top: 78px;
    font-family: "Montserrat", sans-serif;
    font-weight: 700;
    font-size: 27px;
    letter-spacing: 0.5px;
    color: var(--brand-blue);
  }

  .price {
    position: absolute;
    right: 30px;
    bottom: 28px;
    font-weight: 500;
    font-size: 23px;
    color: var(--green-deep);
  }
  .price__amount { color: var(--green-light); }

  .usage-note {
    position: absolute;
    top: 42px;
    left: 0;
    width: 100%;
    text-align: center;
    font-weight: 700;
    font-size: 15.5px;
    line-height: 21px;
    letter-spacing: -0.2px;
    color: var(--brand-blue);
    text-transform: uppercase;
  }

  .contact-box {
    position: absolute;
    left: 58px;
    top: 228px;
    width: 466px;
    height: 97px;
    border: 1px solid var(--green-light);
    border-radius: 28px;
    background: var(--card);
    text-align: center;
    padding-top: 18px;
    font-size: 17px;
    line-height: 21px;
    color: var(--navy);
  }
  .contact-box__label {
    position: absolute;
    left: 50%;
    top: -20px;
    transform: translateX(-50%);
    background: var(--card);
    padding: 6px 10px 2px;
    border-radius: 16px 16px 0 0;
    font-weight: 500;
    font-size: 17px;
    color: var(--navy);
    white-space: nowrap;
  }
  .contact-box__phone { font-weight: 700; color: var(--green-deep); }
  .contact-box__email { font-weight: 600; color: var(--green-light); font-size: 16px; }
</style>
</head>
<body>

<section class="card card--front">
  <svg class="water-art" viewBox="0 0 580 230" preserveAspectRatio="none" role="img" aria-label="Photograph of a clear blue water wave with splashing droplets">
    <defs>
      <linearGradient id="waterFront" x1="0" y1="0" x2="0" y2="1">
        <stop offset="0" stop-color="#ffffff" stop-opacity="0"/>
        <stop offset="0.35" stop-color="#7fa9cc"/>
        <stop offset="0.65" stop-color="#a9c9e0"/>
        <stop offset="1" stop-color="#e6f2f8"/>
      </linearGradient>
    </defs>
    <path d="M0 100 C120 80 200 10 300 40 C400 90 470 140 580 40 L580 230 L0 230 Z" fill="url(#waterFront)"/>
  </svg>
  <div class="brand-name">CEDAR HOLLOW</div>
  <div class="price">PRICE <span class="price__amount">$100</span></div>
</section>

<section class="card card--back">
  <svg class="water-art" viewBox="0 0 580 240" preserveAspectRatio="none" role="img" aria-label="Photograph of a clear blue water wave with splashing droplets">
    <defs>
      <linearGradient id="waterBack" x1="0" y1="0" x2="0" y2="1">
        <stop offset="0" stop-color="#ffffff" stop-opacity="0"/>
        <stop offset="0.35" stop-color="#7fa9cc"/>
        <stop offset="0.65" stop-color="#a9c9e0"/>
        <stop offset="1" stop-color="#e6f2f8"/>
      </linearGradient>
    </defs>
    <path d="M0 100 C120 80 200 10 300 40 C400 90 470 140 580 40 L580 240 L0 240 Z" fill="url(#waterBack)"/>
  </svg>
  <p class="usage-note">This card is to be used to access water refills<br>at any Cedar Hollow water vending machines</p>
  <div class="contact-box">
    <span class="contact-box__label">Please contact</span>
    <span class="contact-box__phone">(869) 418 2930</span> or <span class="contact-box__phone">(869) 534 1276</span><br>
    or <span class="contact-box__email">clearflowbox@mailvista.example</span><br>
    for any assistance or recharging of card
  </div>
</section>

</body>
</html>
```